Business Card Design for Property Development Company Director

I am looking for a professional and unforgettable business card design for our Director of our Property Development Company.
Please see attached .pptx file to find out what information to include. You don't have to follow the exact format shown in the file - I am interested to see your creative flair using the information provided.

```html
<!DOCTYPE html>
<html lang="en">
<head>
<meta charset="utf-8">
<title>Halvern Property Group – Business Card</title>
<link rel="stylesheet" href="https://fonts.googleapis.com/css2?family=Lato:wght@300;400;700&display=swap">
<style>
  :root {
    --backdrop: #2e2a27;
    --card: #0f0f10;
    --card-edge: #1c1c1e;
    --accent-blue: #1a6ccf;
    --mark-grey: #7d7f82;
    --text-light: #d6d6d6;
    --text-muted: #9a9a9a;
    --silver: #e4e4e4;
    --divider: #2c2c2e;
  }
  * { box-sizing: border-box; margin: 0; padding: 0; }
  html, body {
    width: 1200px; height: 844px; overflow: hidden;
    background: var(--backdrop);
    font-family: "Lato", Arial, sans-serif;
  }
  .stage {
    position: relative; width: 1200px; height: 844px;
    display: flex; align-items: center; justify-content: center; gap: 40px;
  }
  .card {
    position: relative; width: 520px; height: 316px;
    background: var(--card);
    border: 1px solid var(--card-edge);
    box-shadow: 0 10px 30px rgba(0,0,0,.45);
    color: var(--text-light);
  }

  /* Front card */
  .card-front .brand-block {
    position: absolute; left: 34px; top: 0; width: 230px; height: 246px;
    display: flex; align-items: center; gap: 12px;
  }
  .brand-block .brand-square {
    width: 22px; height: 22px; background: var(--accent-blue); flex: none;
  }
  .brand-block .brand-name {
    font-weight: 700; font-size: 34px; letter-spacing: 1px; color: var(--mark-grey);
  }
  .card-front .v-divider {
    position: absolute; left: 272px; top: 58px; width: 1px; height: 150px;
    background: var(--divider);
  }
  .card-front .details {
    position: absolute; left: 292px; top: 80px;
  }
  .details .person-name {
    font-weight: 700; font-size: 19px; color: var(--accent-blue);
    text-transform: uppercase; letter-spacing: .3px;
  }
  .details .person-role {
    font-size: 14px; color: var(--text-light); margin-top: 1px; margin-bottom: 16px;
  }
  .contact-list { list-style: none; }
  .contact-list li {
    display: flex; align-items: center; gap: 8px;
    font-size: 15px; line-height: 20px; color: var(--text-light);
  }
  .contact-list svg { width: 11px; height: 11px; fill: var(--text-muted); flex: none; }
  .card-front .h-divider {
    position: absolute; left: 24px; right: 24px; top: 252px; height: 1px;
    background: var(--divider);
  }
  .card-front .licence {
    position: absolute; left: 0; right: 0; top: 266px; text-align: center;
    font-size: 16px; color: var(--text-muted); letter-spacing: .3px;
  }

  /* Back card */
  .card-back { text-align: center; }
  .card-back .specialty {
    position: absolute; left: 0; right: 0; top: 44px;
    font-size: 12px; line-height: 16px; letter-spacing: .6px;
    text-transform: uppercase; color: var(--silver);
  }
  .card-back .brand-lockup {
    position: absolute; left: 0; right: 0; top: 118px;
    display: flex; align-items: center; justify-content: center; gap: 14px;
  }
  .brand-lockup .brand-square {
    width: 26px; height: 26px; background: var(--silver); flex: none;
  }
  .brand-lockup .brand-name {
    font-weight: 400; font-size: 30px; letter-spacing: 3px; color: var(--silver);
    text-transform: uppercase; line-height: 1.05; text-align: left;
  }
  .card-back .invitation {
    position: absolute; left: 0; right: 0; top: 250px;
    font-size: 14px; color: var(--text-light); letter-spacing: .2px;
  }
</style>
</head>
<body>
<main class="stage">
  <section class="card card-front" aria-label="Business card front">
    <div class="brand-block">
      <span class="brand-square"></span>
      <span class="brand-name">HALVERN</span>
    </div>
    <div class="v-divider"></div>
    <div class="details">
      <p class="person-name">Thomas Keller</p>
      <p class="person-role">Director</p>
      <ul class="contact-list">
        <li>
          <svg viewBox="0 0 12 12" aria-hidden="true"><path d="M1 4c0-1.5 2-2.5 5-2.5S11 2.5 11 4v1H8V3.8H4V5H1zM2 6h8l1 5H1z"/></svg>
          0400 318 227
        </li>
        <li>
          <svg viewBox="0 0 12 12" aria-hidden="true"><path d="M0 2h12v8H0zM1 3l5 4 5-4v-.2H1z" fill-rule="evenodd"/></svg>
          thomas@halvern.com.au
        </li>
        <li>
          <svg viewBox="0 0 12 12" aria-hidden="true"><circle cx="6" cy="6" r="5.5"/></svg>
          www.halvern.com.au
        </li>
      </ul>
    </div>
    <div class="h-divider"></div>
    <p class="licence">Real Estate Lic: 5102338 &amp; 5102339</p>
  </section>

  <section class="card card-back" aria-label="Business card back">
    <p class="specialty">Property Development<br>&amp; Site Acquisition Specialists</p>
    <div class="brand-lockup">
      <span class="brand-square"></span>
      <span class="brand-name">Halvern<br>Property Group</span>
    </div>
    <p class="invitation">Ask me about our INVESTMENT &amp; PARTNERSHIP opportunities</p>
  </section>
</main>
</body>
</html>
```